Veldmark Supplies Business Card

Professional business card that stand out to our potential customers. Front and back with clean modern design

Industry/Entity Type

Oil and gas

Contact Information for Business Card

Name, address, website , office phone and cell number

Requirements
Must have
• Editable files for each employee

```html
<!DOCTYPE html>
<html lang="en">
<head>
<meta charset="utf-8">
<title>Veldmark Supplies Business Card</title>
<link href="https://fonts.googleapis.com/css2?family=Archivo:wght@400;700;800&display=swap" rel="stylesheet">
<style>
  :root {
    --stage: #3b3b3d;
    --card-dark: #2a2a2c;
    --card-dark-pattern: #242426;
    --brand-red: #ff0d0d;
    --brand-cyan: #1fb2d6;
    --paper: #ffffff;
    --ink-light: #ffffff;
  }
  * { box-sizing: border-box; margin: 0; padding: 0; }
  html, body { width: 1200px; height: 689px; overflow: hidden; }
  body {
    background: var(--stage);
    font-family: "Archivo", Arial, sans-serif;
    position: relative;
  }
  .card {
    position: absolute;
    top: 195px;
    width: 525px;
    height: 300px;
    border-radius: 18px;
    overflow: hidden;
  }
  .card-back {
    left: 50px;
    background: var(--card-dark);
  }
  .card-back .pattern-fill {
    position: absolute;
    inset: 0;
    background: linear-gradient(135deg, var(--card-dark) 0%, var(--card-dark-pattern) 100%);
  }
  .card-back .back-brand {
    position: absolute;
    top: 28px;
    right: 30px;
    display: flex;
    align-items: center;
    gap: 8px;
    color: var(--brand-red);
    font-weight: 800;
    font-size: 13px;
    letter-spacing: 0.04em;
    text-transform: uppercase;
  }
  .card-back .back-brand .mark-square {
    width: 12px; height: 12px; background: var(--brand-red);
  }
  .card-front {
    left: 625px;
    background: var(--brand-red);
  }
  .card-front .front-shapes {
    position: absolute; inset: 0;
  }
  .brand-block {
    position: absolute;
    top: 72px;
    right: 38px;
    width: 166px;
    display: flex;
    align-items: center;
    gap: 8px;
  }
  .brand-block .mark-square {
    flex: none;
    width: 16px; height: 16px; background: var(--brand-red);
  }
  .brand-block .brand-name {
    color: var(--brand-red);
    font-weight: 800;
    font-size: 19px;
    line-height: 1.05;
    text-transform: uppercase;
    letter-spacing: 0.03em;
  }
  .person {
    position: absolute;
    left: 30px;
    top: 86px;
  }
  .person .name {
    color: var(--brand-cyan);
    font-weight: 700;
    font-size: 21px;
    line-height: 1.2;
  }
  .person .role {
    color: var(--ink-light);
    font-size: 12px;
    line-height: 1.3;
  }
  .contact {
    position: absolute;
    left: 30px;
    bottom: 24px;
    color: var(--ink-light);
    font-size: 12px;
    line-height: 1.35;
  }
  .contact .address { margin-bottom: 10px; }
  .contact ul { list-style: none; }
  .contact li { display: flex; align-items: center; gap: 7px; }
  .contact svg { width: 10px; height: 10px; flex: none; }
</style>
</head>
<body>

  <section class="card card-back" aria-label="Business card back">
    <div class="pattern-fill" role="img" aria-label="Repeating tone-on-tone brand mark pattern"></div>
    <div class="back-brand">
      <span class="mark-square"></span>
      <span>Veldmark Supplies</span>
    </div>
  </section>

  <section class="card card-front" aria-label="Business card front">
    <svg class="front-shapes" viewBox="0 0 525 300" preserveAspectRatio="none" aria-hidden="true">
      <polygon points="318,0 285,182 525,218 525,0" fill="var(--paper)"/>
      <polyline points="333,0 303,165 525,199" fill="none" stroke="var(--brand-cyan)" stroke-width="5"/>
    </svg>

    <div class="brand-block">
      <span class="mark-square"></span>
      <span class="brand-name">Veldmark Supplies</span>
    </div>

    <div class="person">
      <p class="name">Daniel Reyes</p>
      <p class="role">President</p>
    </div>

    <div class="contact">
      <p class="address">4120 Juniper Road<br>Calgary, Canada 20418</p>
      <ul>
        <li>
          <svg viewBox="0 0 10 10"><path d="M2 1l2 2-1 1.2c.6 1.2 1.4 2 2.6 2.6L6.8 6l2 2-1.3 1.3C4.5 9 1 5.5.7 2.3z" fill="var(--brand-cyan)"/></svg>
          555-210-4837
        </li>
        <li>
          <svg viewBox="0 0 10 10"><rect x="2.5" y="0.5" width="5" height="9" rx="1" fill="none" stroke="var(--ink-light)"/></svg>
          555-319-6624
        </li>
        <li>
          <svg viewBox="0 0 10 10"><rect x="0.5" y="2" width="9" height="6.5" fill="var(--ink-light)"/><path d="M0.5 2l4.5 3.5L9.5 2" fill="none" stroke="var(--brand-red)"/></svg>
          info@veldmarksupplies.com
        </li>
        <li>
          <svg viewBox="0 0 10 10"><circle cx="5" cy="5" r="4.5" fill="var(--ink-light)"/><path d="M.5 5h9M5 .5c-2 2.5-2 6.5 0 9M5 .5c2 2.5 2 6.5 0 9" fill="none" stroke="var(--brand-red)" stroke-width="0.8"/></svg>
          www.veldmarksupplies.com
        </li>
      </ul>
    </div>
  </section>

</body>
</html>
```